Judicial election website to attract voters

I need a simple one-page web design for a judicial election. I'm going to put up one picture, maybe two. The picture I have needs a little touch-up (whiten teeth for example). I have 3 paragraphs of text. I'd like a "Donate" button that can link to a CoinDrift account. I'd also like a little background design, like the Constitution or something like that. There's a couple other little things but that's the bulk of it.

Target Market(s)

Involved voters and some media

Industry/Entity Type

Legal

Number of Pages Required

1 page

Font styles to use
Sans Serif

Requirements
Must have
• My picture, text, donate button
• Phrase "Remember to vote August 30, 2016!"
Nice to have
• Perhaps a second photo, maybe a short 30 second video of me talking directly to the voters, cool background: Constitution, something judgey.
Should not have
• Not sure ... profanity, I guess.

```html
<!DOCTYPE html>
<html lang="en">
<head>
<meta charset="utf-8">
<title>Local Elections</title>
<link rel="stylesheet" href="https://fonts.googleapis.com/css2?family=Lato:ital,wght@0,400;0,700;0,900;1,700&family=Catamaran:wght@600;700&display=swap">
<style>
  :root {
    --navy: #263a78;
    --red: #c0272d;
    --red-band: #b8333c;
    --ink: #333333;
    --text: #3a3a3a;
    --page-bg: #f2f2f2;
    --footer: #333333;
    --white: #ffffff;
  }
  * { margin: 0; padding: 0; box-sizing: border-box; }
  html, body { width: 1200px; height: 1128px; overflow: hidden; }
  body {
    position: relative;
    background: linear-gradient(135deg, #f7f7f7 0%, #ececec 40%, #f6f6f6 70%, #eaeaea 100%);
    font-family: "Lato", sans-serif;
    color: var(--text);
  }
  .footer-band {
    position: absolute; left: 0; top: 1034px; width: 1200px; height: 94px;
    background: var(--footer);
  }
  .page {
    position: absolute; left: 171px; top: 0; width: 858px; height: 1063px;
    background: var(--white);
    box-shadow: 0 0 10px rgba(0,0,0,0.08);
  }
  .site-header { position: relative; height: 50px; }
  .brand {
    position: absolute; left: 18px; top: 11px;
    font-family: "Catamaran", sans-serif; font-weight: 700; font-size: 24px;
    letter-spacing: 0.6px; line-height: 1;
  }
  .brand .local { color: var(--navy); }
  .brand .elections { color: var(--red); }
  .follow {
    position: absolute; right: 16px; top: 13px;
    display: flex; align-items: center; gap: 10px;
    font-family: "Catamaran", sans-serif; font-weight: 700; font-size: 16px;
    color: var(--ink); letter-spacing: 0.6px;
  }
  .social { display: flex; align-items: center; gap: 4px; font-family: "Lato", sans-serif; font-weight: 700; font-size: 11px; letter-spacing: 0; }
  .social .dot { width: 12px; height: 12px; border-radius: 50%; }
  .social.circle { color: #3a5797; }
  .social.circle .dot { background: #3a5797; }
  .social.chirp { color: #1d9ad6; }
  .social.chirp .dot { background: #1d9ad6; }

  .hero {
    position: absolute; left: 0; top: 50px; width: 858px; height: 428px;
    background: linear-gradient(180deg, #cfd0d6 0%, #b8b9c2 45%, #8f9099 72%, #4a4a50 100%);
  }
  .hero-arrow { position: absolute; top: 170px; }
  .hero-arrow.prev { left: 25px; }
  .hero-arrow.next { right: 25px; }
  .hero-caption {
    position: absolute; left: 0; right: 0; top: 372px; text-align: center;
    font-family: "Lato", sans-serif; font-weight: 900; font-size: 29px; letter-spacing: 0.3px;
    color: var(--white); text-shadow: 0 2px 3px rgba(0,0,0,0.55);
  }
  .hero-caption .date { color: var(--red); }

  .bio { position: absolute; left: 26px; top: 521px; width: 810px; }
  .portrait-frame {
    position: absolute; left: 0; top: 0; width: 186px; height: 220px;
    border: 2px solid #444; padding: 4px; background: var(--white);
  }
  .portrait { width: 100%; height: 100%; background: linear-gradient(135deg, #b74a52 0%, #d58d7a 50%, #e8a07f 100%); }
  .bio-text { position: absolute; left: 212px; top: 6px; width: 602px; }
  .bio-text p { font-size: 13.6px; line-height: 20.6px; margin-bottom: 12px; color: var(--text); }

  .video { position: absolute; left: 18px; top: 784px; width: 394px; height: 233px; overflow: hidden; }
  .video-still { position: absolute; inset: 0 0 39px 0; background: linear-gradient(160deg, #b6283a 0%, #d9dde6 38%, #c3c8d4 70%, #9fa6b6 100%); }
  .video-play {
    position: absolute; left: 168px; top: 69px; width: 60px; height: 60px; border-radius: 50%;
    background: rgba(45,45,55,0.82);
  }
  .video-controls {
    position: absolute; left: 0; bottom: 0; width: 100%; height: 39px;
    background: linear-gradient(180deg, #3a3d45, #23252b);
  }
  .video-controls .divider { position: absolute; left: 40px; top: 0; width: 1px; height: 39px; background: #15161a; }
  .progress { position: absolute; left: 76px; top: 16px; width: 214px; height: 8px; border-radius: 4px; background: #15161a; }
  .progress .loaded { position: absolute; left: 0; top: 0; width: 132px; height: 8px; border-radius: 4px; background: #3b3e46; }
  .progress .played { position: absolute; left: 2px; top: 2px; width: 98px; height: 4px; border-radius: 2px; background: #1f86cf; }

  .support { position: absolute; left: 446px; top: 784px; width: 394px; height: 234px; overflow: hidden; }
  .support-bg { position: absolute; inset: 0; background: linear-gradient(135deg, #2f2f2f 0%, #555 50%, #3a3a3a 100%); }
  .support-title {
    position: absolute; left: 0; top: 0; width: 100%; height: 43px;
    background: rgba(190,52,62,0.92); color: var(--white); text-align: center;
    font-family: "Catamaran", sans-serif; font-weight: 700; font-size: 23px; letter-spacing: 1px; line-height: 45px;
  }
  .support-note {
    position: absolute; left: 0; top: 60px; width: 100%; text-align: center;
    font-style: italic; font-weight: 700; font-size: 16.5px; line-height: 26px; color: var(--white);
  }
  .donate {
    position: absolute; left: 113px; top: 131px; width: 167px; height: 35px; display: flex;
    background: var(--red); color: var(--white); text-decoration: none;
  }
  .donate .icon { width: 39px; height: 35px; background: #8f1b21; display: flex; align-items: center; justify-content: center; }
  .donate .label { flex: 1; text-align: center; font-family: "Catamaran", sans-serif; font-weight: 700; font-size: 16.5px; letter-spacing: 0.6px; line-height: 37px; }
  .pay-brand {
    position: absolute; left: 0; top: 192px; width: 100%; text-align: center;
    font-family: "Lato", sans-serif; font-weight: 900; font-size: 22px; color: #5aaee8;
  }

  .copyright {
    position: absolute; left: 0; top: 1086px; width: 1200px; text-align: center;
    font-size: 14px; color: var(--white);
  }
</style>
</head>
<body>
  <div class="footer-band"></div>
  <main class="page">
    <header class="site-header">
      <div class="brand"><span class="local">LOCAL</span> <span class="elections">ELECTIONS</span></div>
      <div class="follow">
        FOLLOW US :
        <span class="social circle"><span class="dot"></span>Circlebook</span>
        <span class="social chirp"><span class="dot"></span>Chirper</span>
      </div>
    </header>

    <section class="hero" role="img" aria-label="Row of voting booths with a voter casting a ballot">
      <svg class="hero-arrow prev" width="22" height="90" viewBox="0 0 22 90"><polyline points="20,2 2,45 20,88" fill="none" stroke="#fff" stroke-width="2"/></svg>
      <svg class="hero-arrow next" width="22" height="90" viewBox="0 0 22 90"><polyline points="2,2 20,45 2,88" fill="none" stroke="#fff" stroke-width="2"/></svg>
      <h1 class="hero-caption">Remember to Vote <span class="date">August 30, 2016!</span></h1>
    </section>

    <section class="bio">
      <div class="portrait-frame"><div class="portrait" role="img" aria-label="Portrait of the candidate in front of a flag"></div></div>
      <div class="bio-text">
        <p>Lorem ipsum dolor sit amet, consectetur adipiscing elit. Sed vitae magna tellus. Aenean ante nunc, semper nec cursus non, rutrum ac eros. Vestibulum mattis justo ac dui bibendum consequat a ac ipsum. Praesent a arcu venenatis, auctor velit eu, suscipit libero.</p>
        <p>Lorem ipsum dolor sit amet, consectetur adipiscing elit. Sed vitae magna tellus. Aenean ante nunc, semper nec cursus non, rutrum ac eros. Vestibulum mattis justo ac dui bibendum consequat a ac ipsum. Praesent a arcu venenatis, auctor velit eu, suscipit libero.</p>
        <p>Lorem ipsum dolor sit amet, consectetur adipiscing elit. Sed vitae magna tellus. Aenean ante nunc, semper nec cursus non, rutrum ac eros. Vestibulum mattis justo ac dui bibendum consequat a ac ipsum. Praesent a arcu venenatis, auctor velit eu, suscipit libero.</p>
      </div>
    </section>

    <section class="video">
      <div class="video-still" role="img" aria-label="Finger selecting a choice on an electronic ballot screen"></div>
      <div class="video-play">
        <svg width="60" height="60" viewBox="0 0 60 60"><polygon points="24,19 42,30 24,41" fill="#fff"/></svg>
      </div>
      <div class="video-controls">
        <svg style="position:absolute;left:14px;top:13px" width="14" height="14" viewBox="0 0 14 14"><polygon points="2,1 13,7 2,13" fill="#fff"/></svg>
        <div class="divider"></div>
        <svg style="position:absolute;left:49px;top:13px" width="20" height="14" viewBox="0 0 20 14"><polygon points="1,5 5,5 10,1 10,13 5,9 1,9" fill="#fff"/><path d="M13 4 Q15 7 13 10 M15.5 2.5 Q19 7 15.5 11.5" fill="none" stroke="#fff" stroke-width="1.2"/></svg>
        <div class="progress"><div class="loaded"></div><div class="played"></div></div>
      </div>
    </section>

    <section class="support">
      <div class="support-bg" role="img" aria-label="Cupped hands holding a young seedling"></div>
      <h2 class="support-title">SUPPORT THE CAMPAIGN</h2>
      <p class="support-note">Your contributions make this<br>campaign possible.</p>
      <a class="donate" href="#">
        <span class="icon">
          <svg width="26" height="16" viewBox="0 0 26 16"><rect x="1" y="4" width="5" height="10" fill="none" stroke="#fff" stroke-width="1.4"/><path d="M6 6 L12 3 L22 3 Q24 4 22 6 L15 6 M6 13 L18 13 Q20 12 18 10 L13 10" fill="none" stroke="#fff" stroke-width="1.4"/></svg>
        </span>
        <span class="label">DONATE NOW</span>
      </a>
      <div class="pay-brand">CoinDrift</div>
    </section>
  </main>
  <p class="copyright">Copyright © 2016 LOCAL ELECTIONS. &nbsp; All Rights Reserved</p>
</body>
</html>
```